Flat bootstrap design for existing site

I'm looking for a modern flat design based around an existing logo. This has to be a custom design (no external templates), and implemented into a bootstrap framework.

The logo is attached as 2 versions - choose whichever you want, that flows better with whatever design you choose.

Added screenshots of the existing site (currently using the default bootstrap layouts). Please make your designs around those pages in the screenshots (i.e. the homepage only has the postal code input and the header). The active page has 3 screenshots, because I wanted to illustrate the other states that would be visible (in the table rows).

This is a moving/junk removal website, just for some context.

Here's some example websites (flat designs) that I like, just to give you an idea of what I'm after.

https://www.plimvora.com/
https://dacklow.com/
https://trevanu.com/
https://quobrintal.com/en/

Coding

Coded - Design and coding required

Number of Pages Required

5+ page

Colors

Designer to choose colors to be used in the design.

Requirements
Must have
• It must be a modern/simple flat design, that is built around the existing logo (attached).
• It has to be implemented using bootstrap.

```html
<!DOCTYPE html>
<html lang="en">
<head>
<meta charset="utf-8">
<title>Drovalo – Sign in</title>
<link href="https://fonts.googleapis.com/css2?family=Open+Sans:wght@400;600&display=swap" rel="stylesheet">
<style>
  :root {
    --accent: #4cc9f5;
    --page-bg: #f8f8f8;
    --white: #ffffff;
    --line: #e6e6e6;
    --input-line: #d9d9d9;
    --text-dark: #333333;
    --text-nav: #555555;
    --text-muted: #777777;
    --button: #2566a4;
  }
  * { box-sizing: border-box; margin: 0; padding: 0; }
  html, body {
    width: 1200px; height: 902px; overflow: hidden;
    font-family: "Open Sans", Arial, sans-serif;
    background: var(--page-bg);
    color: var(--text-dark);
  }
  .site-header {
    position: absolute; top: 0; left: 0; width: 1200px; height: 88px;
    background: var(--white);
    border-top: 3px solid var(--accent);
    border-bottom: 1px solid var(--line);
  }
  .brand {
    position: absolute; left: 131px; top: 27px;
    display: flex; align-items: center; gap: 8px;
    font-size: 26px; font-weight: 600; color: var(--accent);
    letter-spacing: 0.5px; text-decoration: none;
  }
  .brand-dot {
    width: 20px; height: 20px; border-radius: 50%; background: var(--accent);
  }
  .main-nav a {
    position: absolute; top: 0; height: 85px;
    display: flex; align-items: center; justify-content: center;
    font-size: 13px; color: var(--text-nav); text-decoration: none;
    text-transform: uppercase;
  }
  .nav-book { left: 560px; width: 80px; }
  .nav-how { left: 678px; width: 120px; }
  .nav-driver { left: 825px; width: 173px; background: var(--accent); color: var(--white) !important; }
  .nav-signin { left: 1006px; width: 80px; }
  .signin-card {
    position: absolute; left: 132px; top: 121px; width: 936px; height: 311px;
    background: var(--white); border: 1px solid var(--line);
  }
  .signin-title {
    position: absolute; top: 46px; width: 100%; text-align: center;
    font-size: 34px; font-weight: 600; color: var(--text-dark);
  }
  .field {
    position: absolute; left: 253px; width: 428px; height: 39px;
    border: 1px solid var(--input-line); border-radius: 2px;
    padding: 0 12px; display: flex; align-items: center;
    font-size: 12px; color: var(--text-muted); background: var(--white);
  }
  .field-email { top: 113px; }
  .field-password { top: 161px; }
  .btn-login {
    position: absolute; left: 421px; top: 210px; width: 93px; height: 38px;
    background: var(--button); color: var(--white); border: none; border-radius: 2px;
    font-family: "Open Sans", Arial, sans-serif; font-size: 13.5px; font-weight: 600;
    display: flex; align-items: center; justify-content: center;
  }
  .site-footer {
    position: absolute; top: 845px; left: 0; width: 1200px; height: 57px;
    background: var(--white); border-top: 1px solid var(--line);
    display: flex; align-items: center; justify-content: center;
    font-size: 11.5px; color: var(--text-muted);
  }
</style>
</head>
<body>
  <header class="site-header">
    <a class="brand" href="#"><span class="brand-dot"></span>Drovalo</a>
    <nav class="main-nav">
      <a class="nav-book" href="#">Book</a>
      <a class="nav-how" href="#">How it works</a>
      <a class="nav-driver" href="#">Become a driver</a>
      <a class="nav-signin" href="#">Sign in</a>
    </nav>
  </header>

  <main class="signin-card">
    <h1 class="signin-title">Please Sign in</h1>
    <div class="field field-email">E-mail Address</div>
    <div class="field field-password">Password</div>
    <button class="btn-login">LOG IN</button>
  </main>

  <footer class="site-footer">Copyrights © Drovalo . 2017 | All rights reserved.</footer>
</body>
</html>
```